Business card for Luxury Portable Restroom Trailer company

We are a Luxury Portable Restroom Trailer Company Called FALCRIDGE HIRES. Based in Orange County California. We provide portable restroom trailers for events, such as, Weddings, Concerts, Charity events, Sporting events, Tournaments, Corporate events, ect. We rent and Sell the Luxury restrooms. Our colors are white, grey, and Orange. As you will see in the logo we uploaded.
There are 2 people in the company so the names and titles will change for the 3 people but card will remain the same. Here is the information for each Person: Dwight Penner CFO 555 318-0476
next Person: Leon Marchetti VP 555 318-0476
Next Person: Owen Marchetti CEO 555 318-0476
Information to include on the card: Luxury Restroom Trailers Rental and Sales. Weddings, Concerts, Charity, Sporting and Corp. Events.

```html
<!DOCTYPE html>
<html lang="en">
<head>
<meta charset="utf-8">
<title>FALCRIDGE HIRES – Business Card</title>
<link rel="stylesheet" href="https://fonts.googleapis.com/css2?family=Open+Sans:wght@400;600;700;800&display=swap">
<style>
  :root {
    --bg: #222222;
    --orange: #ee6a25;
    --grey: #555555;
    --grey-dark: #3a3a3a;
    --grey-mid: #5c5c5c;
    --white: #ffffff;
    --ink: #333333;
  }
  * { margin: 0; padding: 0; box-sizing: border-box; }
  html, body { width: 1200px; height: 768px; overflow: hidden; }
  body {
    background: var(--bg);
    font-family: "Open Sans", Arial, sans-serif;
    position: relative;
  }
  .card {
    position: absolute;
    top: 224px;
    width: 560px;
    height: 320px;
    overflow: hidden;
    box-shadow: 0 10px 30px rgba(0,0,0,.5);
  }
  /* Back */
  .card--back { left: 26px; background: var(--grey-dark); }
  .back-pattern {
    position: absolute; inset: 0;
    background: linear-gradient(160deg, #6a6a6a 0%, #4a4a4a 45%, #2e2e2e 100%);
  }
  .back-brand {
    position: absolute; right: 40px; bottom: 110px;
    border: 3px solid var(--orange);
    padding: 8px 14px;
    background: var(--grey-dark);
    display: flex; align-items: center; gap: 8px;
  }
  /* Shared brand lockup */
  .brand-mark { width: 12px; height: 12px; background: var(--orange); flex: none; }
  .brand-name {
    font-weight: 800; color: var(--orange);
    letter-spacing: 1px; line-height: 1; white-space: nowrap;
  }
  .back-brand .brand-name { font-size: 20px; }

  /* Front */
  .card--front { left: 614px; background: var(--white); }
  .front-brand {
    position: absolute; left: 50%; top: 52px; transform: translateX(-50%);
    border: 3px solid var(--orange);
    padding: 14px 22px;
    display: flex; align-items: center; gap: 10px;
  }
  .front-brand .brand-name { font-size: 30px; }

  .person {
    position: absolute; right: 322px; top: 170px; text-align: right;
  }
  .person-name { font-size: 28px; font-weight: 700; line-height: 1.1; white-space: nowrap; }
  .person-name .first { color: var(--orange); }
  .person-name .last { color: var(--grey); }
  .person-title { font-size: 13px; font-weight: 600; color: var(--ink); margin-top: 2px; }

  .divider {
    position: absolute; left: 262px; top: 168px;
    width: 1px; height: 60px; background: var(--ink);
  }

  .contacts {
    position: absolute; left: 286px; top: 164px;
    list-style: none;
    font-size: 13px; color: var(--ink); line-height: 22px;
  }
  .contacts li { display: flex; align-items: center; gap: 8px; }
  .contacts svg { width: 12px; height: 12px; fill: var(--orange); flex: none; }

  .services {
    position: absolute; left: 0; right: 0; bottom: 0; height: 58px;
    background: var(--orange);
    color: var(--white);
    font-size: 13px; font-weight: 600;
    display: flex; flex-direction: column; justify-content: center; align-items: center;
    line-height: 20px;
  }
  .services .sep {
    display: inline-block; width: 6px; height: 6px; background: var(--white);
    margin: 0 6px; vertical-align: middle;
  }
</style>
</head>
<body>

  <section class="card card--back" aria-label="Card back">
    <div class="back-pattern" role="img" aria-label="Repeating brand-symbol pattern in grey tones"></div>
    <div class="back-brand">
      <span class="brand-mark"></span>
      <span class="brand-name">FALCRIDGE HIRES</span>
    </div>
  </section>

  <section class="card card--front" aria-label="Card front">
    <div class="front-brand">
      <span class="brand-mark"></span>
      <span class="brand-name">FALCRIDGE HIRES</span>
    </div>

    <div class="person">
      <div class="person-name"><span class="first">Dwight</span> <span class="last">Penner</span></div>
      <div class="person-title">CFO</div>
    </div>

    <div class="divider"></div>

    <ul class="contacts">
      <li>
        <svg viewBox="0 0 24 24" aria-hidden="true"><path d="M6.6 10.8a15.1 15.1 0 0 0 6.6 6.6l2.2-2.2a1 1 0 0 1 1-.25 11.4 11.4 0 0 0 3.6.57 1 1 0 0 1 1 1V20a1 1 0 0 1-1 1A17 17 0 0 1 3 4a1 1 0 0 1 1-1h3.5a1 1 0 0 1 1 1c0 1.25.2 2.45.57 3.57a1 1 0 0 1-.25 1z"/></svg>
        555 318-0476
      </li>
      <li>
        <svg viewBox="0 0 24 24" aria-hidden="true"><path d="M2 5h20v14H2z M2 5l10 8 10-8" stroke="#fff" stroke-width="1.5"/></svg>
        info@falcridgehires.com
      </li>
      <li>
        <svg viewBox="0 0 24 24" aria-hidden="true"><circle cx="12" cy="12" r="10"/><path d="M2 12h20M12 2c3 3 3 17 0 20M12 2c-3 3-3 17 0 20" stroke="#fff" stroke-width="1.5" fill="none"/></svg>
        www.falcridgehires.com
      </li>
    </ul>

    <div class="services">
      <div><span class="sep"></span>Luxury Restroom Trailers Rental and Sales</div>
      <div><span class="sep"></span>Weddings <span class="sep"></span>Concerts <span class="sep"></span>Charity <span class="sep"></span>Sporting and Corp <span class="sep"></span>Events</div>
    </div>
  </section>

</body>
</html>
```